Local Flower Farm Needs Business Card Design

I need business cards designed for a flower farm based in Eudora, Kansas.
Business Info:
We are a local cut flower farm located in Eudora, Kansas, founded by Corinne Haldwick. What started as a passion for agriculture and search for more joy in daily life has blossomed into a small business dedicated to providing the community with beautiful, fresh, and sustainable flowers. We specialize in local, seasonal blooms, ensuring that every petal reflects the care and dedication we pour into our craft. Our mission is to deliver the highest quality flowers directly to our customers through local farmers markets and to florists who share our commitment to sustainability. Join us in celebrating the beauty of nature, one bloom at a time!
Contact Details:
Corinne Haldwick
Owner
Phone 913-555-0147
Facebook: Rosalind Thorpe Gardens
Instagram: @RosalindThorpeGardens
Website: RosalindThorpeGardens.example
Target Market(s)
Wholesale to Florists and Direct to Consumer via Farmers Market
Industry/Entity Type
Florist, Farm
Contact Information for Business Card
Name, Contact Info, Logo
Look and feel
Each slider illustrates characteristics of the customer's brand and the style your logo design should communicate.

```html
<!DOCTYPE html>
<html lang="en">
<head>
<meta charset="utf-8">
<title>Rosalind Thorpe Gardens – Business Card</title>
<link rel="stylesheet" href="https://fonts.googleapis.com/css2?family=Cormorant+Garamond:wght@500&family=Lato:wght@400&display=swap">
<style>
  :root {
    --backdrop: #3b3b3b;
    --card-front: #f1f1f0;
    --card-back: #ffffff;
    --ink: #12302f;
    --text: #1c1c1c;
    --muted: #444444;
  }
  * { margin: 0; padding: 0; box-sizing: border-box; }
  html, body { width: 1200px; height: 1000px; overflow: hidden; }
  body { background: var(--backdrop); position: relative; font-family: "Lato", sans-serif; }

  .card {
    position: absolute;
    left: 200px;
    width: 800px;
    border-radius: 18px;
  }
  .card--front { top: 22px; height: 458px; background: var(--card-front); }
  .card--back { top: 498px; height: 457px; background: var(--card-back); }

  .brand-mark {
    position: absolute;
    display: flex;
    align-items: center;
    justify-content: center;
    border: 1.5px solid var(--ink);
    border-radius: 50%;
    transform: translate(-50%, -50%);
    font-family: "Cormorant Garamond", serif;
    font-weight: 500;
    color: var(--ink);
    text-transform: uppercase;
    line-height: 1.12;
    text-align: center;
  }
  .card--front .brand-mark {
    left: 400px; top: 223px;
    width: 288px; height: 288px;
    font-size: 36px; letter-spacing: 3px;
  }
  .card--back .brand-mark {
    left: 392px; top: 157px;
    width: 206px; height: 206px;
    font-size: 25px; letter-spacing: 2px;
  }

  .holder {
    position: absolute;
    left: 204px; top: 318px;
    transform: translateX(-50%);
    text-align: center;
    white-space: nowrap;
  }
  .holder__name {
    font-family: "Cormorant Garamond", serif;
    font-weight: 500;
    font-size: 30px;
    letter-spacing: 1px;
    text-transform: uppercase;
    color: var(--ink);
  }
  .holder__role { font-size: 17px; color: var(--muted); margin-top: 4px; }

  .divider {
    position: absolute;
    left: 400px; top: 300px;
    width: 2px; height: 128px;
    background: var(--text);
  }

  .contact-list {
    position: absolute;
    left: 440px; top: 305px;
    list-style: none;
  }
  .contact-list__item {
    display: flex; align-items: center;
    height: 28.5px;
    font-size: 21px;
    color: var(--text);
    white-space: nowrap;
  }
  .contact-list__icon { width: 16px; height: 16px; margin-right: 9px; flex: none; }
</style>
</head>
<body>
  <section class="card card--front">
    <div class="brand-mark">Rosalind<br>Thorpe<br>Gardens</div>
  </section>

  <section class="card card--back">
    <div class="brand-mark">Rosalind<br>Thorpe<br>Gardens</div>

    <div class="holder">
      <div class="holder__name">Corinne Haldwick</div>
      <div class="holder__role">Owner</div>
    </div>

    <div class="divider"></div>

    <ul class="contact-list">
      <li class="contact-list__item">
        <svg class="contact-list__icon" viewBox="0 0 16 16" aria-hidden="true">
          <path d="M3 1.5l2.6 0.4 1 3-1.6 1.2c0.8 1.8 2.1 3.1 3.9 3.9l1.2-1.6 3 1 0.4 2.6-1.7 1.6C6.6 13.4 2.6 9.4 1.4 3.2z" fill="var(--text)"/>
        </svg>
        913-555-0147
      </li>
      <li class="contact-list__item">
        <svg class="contact-list__icon" viewBox="0 0 16 16" aria-hidden="true">
          <circle cx="8" cy="8" r="6" fill="var(--text)"/>
        </svg>
        Rosalind Thorpe Gardens
      </li>
      <li class="contact-list__item">
        <svg class="contact-list__icon" viewBox="0 0 16 16" aria-hidden="true">
          <rect x="2" y="2" width="12" height="12" rx="2" fill="none" stroke="var(--text)" stroke-width="1.8"/>
        </svg>
        @RosalindThorpeGardens
      </li>
      <li class="contact-list__item">
        <svg class="contact-list__icon" viewBox="0 0 16 16" aria-hidden="true">
          <circle cx="8" cy="8" r="6.5" fill="none" stroke="var(--text)" stroke-width="1.5"/>
          <ellipse cx="8" cy="8" rx="2.8" ry="6.5" fill="none" stroke="var(--text)" stroke-width="1.2"/>
          <line x1="1.5" y1="8" x2="14.5" y2="8" stroke="var(--text)" stroke-width="1.2"/>
        </svg>
        RosalindThorpeGardens.example
      </li>
    </ul>
  </section>
</body>
</html>
```